Letterhead and business cards for criminal defense law firm
with existing logo
Letterhead and business cards for criminal defense law firm - Law
Creative Brief
Simple
The Law Office of Marcus Tarvic, PLLC
718 Corbel Avenue, Suite 300 Houston, TX 77019
Tarvic@BrindleCounselGroup.net
I would like to incorporate our slogan: Experienced criminal defense lawyers Or if you think of a better slogan/motto, feel free to incorporate it. I am not a flashy or showy lawyer. I want the card to invoke credibility, stability and intelligence (not an ambulance chaser or sleazy lawyer).

```html
<!DOCTYPE html>
<html lang="en">
<head>
<meta charset="utf-8">
<title>Marcus Tarvic, PLLC — Business Cards</title>
<link rel="stylesheet" href="https://fonts.googleapis.com/css2?family=Open+Sans:wght@400;600;700&display=swap">
<style>
  :root {
    --navy: #1f2553;
    --navy-deep: #161b40;
    --slate: #55565c;
    --paper: #ffffff;
    --ink: #2b2d35;
    --muted: #6b6d75;
    --stage: #e6e7ea;
  }
  * { box-sizing: border-box; margin: 0; padding: 0; }
  html, body { width: 1200px; height: 901px; overflow: hidden; }
  body {
    background: var(--stage);
    font-family: "Open Sans", Arial, sans-serif;
    display: flex; align-items: center; justify-content: center; gap: 60px;
  }
  .card {
    width: 525px; height: 300px; position: relative; overflow: hidden;
    box-shadow: 0 10px 28px rgba(0,0,0,.18);
  }
  .card-back { background: var(--navy); color: var(--paper); }
  .card-front { background: var(--paper); color: var(--ink); }

  .firm-mark { display: flex; align-items: center; gap: 12px; }
  .firm-mark .square { width: 34px; height: 34px; background: var(--navy); }
  .firm-mark .name {
    font-weight: 700; font-size: 24px; letter-spacing: .04em; text-transform: uppercase;
    color: var(--navy);
  }
  .card-back .firm-mark { position: absolute; left: 50%; top: 50%; transform: translate(-50%,-50%); }
  .card-back .firm-mark .square { background: var(--paper); }
  .card-back .firm-mark .name { color: var(--paper); }
  .card-back .rule {
    position: absolute; left: 24px; right: 24px; top: 24px; bottom: 24px;
    border: 1px solid rgba(255,255,255,.18);
  }

  .card-front .firm-mark { position: absolute; left: 34px; top: 30px; }
  .tagline {
    position: absolute; left: 80px; top: 70px;
    font-size: 9px; letter-spacing: .08em; text-transform: uppercase; color: var(--muted);
  }
  .person { position: absolute; left: 34px; top: 104px; }
  .person .name { font-size: 17px; color: var(--ink); }
  .person .title { font-size: 9px; color: var(--muted); margin-top: 1px; }
  .address { position: absolute; left: 34px; top: 152px; font-size: 9px; line-height: 1.45; color: var(--muted); width: 150px; }
  .contacts {
    position: absolute; left: 34px; top: 192px;
    display: grid; grid-template-columns: 150px auto; row-gap: 4px;
    font-size: 9px; color: var(--muted);
  }
  .contacts .item { display: flex; align-items: center; gap: 6px; }
  .contacts svg { width: 9px; height: 9px; fill: var(--slate); }
  .waves { position: absolute; left: 0; bottom: 0; width: 525px; height: 150px; }
</style>
</head>
<body>
  <section class="card card-back" aria-label="Business card back">
    <div class="rule"></div>
    <div class="firm-mark">
      <span class="square"></span>
      <span class="name">Marcus Tarvic</span>
    </div>
  </section>

  <section class="card card-front" aria-label="Business card front">
    <div class="firm-mark">
      <span class="square"></span>
      <span class="name">Marcus Tarvic</span>
    </div>
    <p class="tagline">Experienced Criminal Defense Lawyers</p>

    <div class="person">
      <p class="name">Marcus Tarvic</p>
      <p class="title">Attorney at Law</p>
    </div>
    <p class="address">718 Corbel Avenue, Suite 300<br>Houston, TX 77019</p>

    <div class="contacts">
      <span class="item"><svg viewBox="0 0 10 10"><path d="M2 0h2l1 3-1.5 1a6 6 0 0 0 2.5 2.5L7 5l3 1v2a2 2 0 0 1-2 2A8 8 0 0 1 0 2a2 2 0 0 1 2-2z"/></svg>713-555-0142</span>
      <span class="item"><svg viewBox="0 0 10 10"><path d="M0 2h10v6H0z"/></svg>Tarvic@BrindleCounselGroup.net</span>
      <span class="item"><svg viewBox="0 0 10 10"><path d="M1 3h8v6H1zM3 0h4v3H3z"/></svg>713-555-0187</span>
      <span class="item"><svg viewBox="0 0 10 10"><circle cx="5" cy="5" r="4.5"/></svg>BrindleCounselGroup.net</span>
    </div>

    <svg class="waves" viewBox="0 0 525 150" preserveAspectRatio="none" aria-hidden="true">
      <path d="M0 150 L0 132 C140 150 300 120 525 48 L525 150 Z" fill="var(--navy)"/>
      <path d="M0 120 C150 140 310 105 525 32" stroke="var(--slate)" stroke-width="6" fill="none"/>
      <path d="M0 104 C160 122 320 92 525 18" stroke="var(--slate)" stroke-width="3" fill="none"/>
      <path d="M260 150 C360 135 450 108 525 78 L525 150 Z" fill="var(--navy-deep)"/>
    </svg>
  </section>
</body>
</html>
```